Vantro cards

I am in the auto motive, transportation business I would like a business card that is Something cool, modern edgy, having to do with car culture. I offer towing service for high and exotic cars. I also provide towing for collisions and car accidents. I offer open and enclosed transport nationwide.

Target Market(s)

Car culture people high end auto collectors

Industry/Entity Type

Towing car carrier

Contact Information for Business Card

My company colors black yellow and silver

Font styles to use
Serif

```html
<!DOCTYPE html>
<html lang="en">
<head>
<meta charset="utf-8">
<title>Vantro business cards</title>
<link rel="stylesheet" href="https://fonts.googleapis.com/css2?family=Montserrat:wght@400;600;700&display=swap">
<style>
  :root{
    --stage:#3a3330;
    --card:#181818;
    --card-deep:#111111;
    --yellow:#f5d63d;
    --white:#f2f2f2;
    --silver:#b9b9b9;
    --shadow-tone:#2a2a2a;
  }
  *{box-sizing:border-box;margin:0;padding:0}
  html,body{width:1200px;height:786px;overflow:hidden}
  body{background:var(--stage);font-family:"Montserrat",sans-serif;position:relative}
  .card{position:absolute;width:540px;height:309px;background:var(--card);overflow:hidden;box-shadow:0 10px 28px rgba(0,0,0,.45)}
  .card--front{left:36px;top:239px}
  .card--back{left:624px;top:239px}
  .truck-art{position:absolute;background:radial-gradient(ellipse at 45% 40%,#4a4a4a 0%,#2b2b2b 45%,var(--card) 80%)}
  .card--front .truck-art{left:250px;top:30px;width:270px;height:220px}
  .card--back .truck-art{left:40px;top:50px;width:330px;height:210px}
  .stripe{position:absolute;left:0;right:0;height:4px;background:var(--yellow);top:262px}
  .brand{position:absolute;display:flex;align-items:center;gap:10px}
  .brand__dot{width:16px;height:16px;border-radius:50%;background:var(--yellow)}
  .brand__name{font-weight:700;color:var(--yellow);text-transform:uppercase;letter-spacing:1px}
  .card--front .brand{left:34px;top:46px}
  .card--front .brand__name{font-size:30px}
  .card--back .brand{left:270px;top:96px}
  .card--back .brand__name{font-size:38px}
  .person{position:absolute;left:34px;top:112px}
  .person__name{font-weight:700;font-size:19px;color:var(--yellow)}
  .person__role{font-size:11px;color:var(--silver);margin-top:2px}
  .person__rule{width:14px;height:2px;background:var(--yellow);margin-top:8px}
  .address{position:absolute;left:34px;top:170px;font-size:11px;line-height:14px;color:var(--white)}
  .contacts{position:absolute;left:34px;top:206px;list-style:none;font-size:11px;line-height:15px;color:var(--white)}
  .contacts li{display:flex;align-items:center;gap:7px}
  .contacts svg{width:9px;height:9px;fill:var(--yellow)}
</style>
</head>
<body>
  <section class="card card--front">
    <div class="truck-art" role="img" aria-label="Faint silhouette of a flatbed tow truck"></div>
    <div class="brand"><span class="brand__dot"></span><span class="brand__name">Vantro</span></div>
    <div class="person">
      <p class="person__name">Marcus Doyle</p>
      <p class="person__role">Owner</p>
      <div class="person__rule"></div>
    </div>
    <p class="address">48 Orchard Lane<br>Fenwick, PA 17000</p>
    <ul class="contacts">
      <li><svg viewBox="0 0 10 10"><path d="M2 0h2l1 3-1.5 1a6 6 0 0 0 2.5 2.5L7 5l3 1v2a2 2 0 0 1-2 2A8 8 0 0 1 0 2a2 2 0 0 1 2-2z"/></svg>(555) 014-2290</li>
      <li><svg viewBox="0 0 10 10"><path d="M0 2h10v6H0z M0 2l5 3.5L10 2" fill="none" stroke="#f5d63d" stroke-width="1.2"/></svg>info@vantrotransportation.com</li>
      <li><svg viewBox="0 0 10 10"><circle cx="5" cy="5" r="4.4" fill="none" stroke="#f5d63d" stroke-width="1.1"/><path d="M.6 5h8.8M5 .6c-2.5 2.6-2.5 6.2 0 8.8M5 .6c2.5 2.6 2.5 6.2 0 8.8" fill="none" stroke="#f5d63d" stroke-width=".9"/></svg>www.vantrotransportation.com</li>
    </ul>
    <div class="stripe"></div>
  </section>

  <section class="card card--back">
    <div class="truck-art" role="img" aria-label="Faint silhouette of a flatbed tow truck"></div>
    <div class="brand"><span class="brand__dot"></span><span class="brand__name">Vantro</span></div>
    <div class="stripe"></div>
  </section>
</body>
</html>
```